Torvane Halbridge

Looking for modern business cards.
Clean contemporary design.
Similar to this.
https://www.plumvexa-search.example/imgres?imgurl=https%3A%2F%2Fimg.quorlint-cdn.example%2Fsleek_dark_metal_card_design_540.jpg&imgrefurl=https%3A%2F%2Fwww.quorlint-prints.example%2Fsleek_dark_metal_card_design-918273645501928374&q=modern%20business%20cards

But I'd like the blue to look metallic.

Business

```html
<!DOCTYPE html>
<html lang="en">
<head>
<meta charset="utf-8">
<title>Torvane Halbridge – Business Cards</title>
<link rel="stylesheet" href="https://fonts.googleapis.com/css2?family=Open+Sans:wght@300;400;600&family=Roboto+Condensed:wght@400;700&display=swap">
<style>
  :root {
    --stage: #e9e7e3;
    --paper: #ffffff;
    --teal: #2aa6c4;
    --teal-light: #5cc6de;
    --teal-deep: #1d86a3;
    --navy: #245571;
    --navy-light: #3a7394;
    --navy-deep: #173d54;
    --accent: #ee4a2c;
    --ink-logo: #2b5f7c;
    --ink-muted: #4b4b4b;
  }
  * { box-sizing: border-box; margin: 0; padding: 0; }
  html, body { width: 1200px; height: 886px; overflow: hidden; background: var(--stage); }
  .canvas { position: relative; width: 1200px; height: 886px; }

  .card {
    position: absolute; top: 288px; width: 540px; height: 310px;
    background: var(--paper); overflow: hidden;
    box-shadow: 0 10px 28px rgba(0,0,0,.18);
  }
  .card--front { left: 45px; }
  .card--back { left: 615px; }

  .brand { position: absolute; left: 40px; top: 52px; }
  .brand__name {
    display: flex; align-items: center; gap: 10px;
    font-family: "Open Sans", sans-serif; font-weight: 300;
    font-size: 31px; line-height: 1.2; color: var(--ink-logo); letter-spacing: -.5px;
  }
  .brand__dot { width: 12px; height: 12px; border-radius: 50%; background: var(--accent); flex: none; }
  .brand__tagline {
    margin-top: 6px; font-family: "Open Sans", sans-serif; font-weight: 600;
    font-size: 9px; color: var(--teal-deep); letter-spacing: .4px;
  }

  .band--teal {
    position: absolute; left: 0; right: 0; top: 150px; height: 70px;
    background: linear-gradient(180deg, var(--teal-light) 0%, var(--teal) 45%, var(--teal-deep) 80%, var(--teal) 100%);
  }
  .band--navy {
    position: absolute; left: 0; right: 0; top: 220px; bottom: 0;
    background: linear-gradient(180deg, var(--navy-light) 0%, var(--navy) 40%, var(--navy-deep) 75%, var(--navy) 100%);
  }
  .band--teal::after, .band--navy::after {
    content: ""; position: absolute; inset: 0;
    background: linear-gradient(100deg, transparent 30%, rgba(255,255,255,.14) 48%, transparent 62%);
  }

  .person {
    position: absolute; left: 290px; top: 160px; z-index: 2;
    font-family: "Roboto Condensed", sans-serif; color: #fff;
  }
  .person__name { font-weight: 700; font-size: 20px; line-height: 24px; letter-spacing: .3px; }
  .person__role { font-weight: 400; font-size: 13px; line-height: 16px; letter-spacing: .5px; }

  .timeline { position: absolute; left: 0; top: 208px; z-index: 2; }

  .contact {
    position: absolute; left: 60px; top: 236px; z-index: 2;
    font-family: "Roboto Condensed", sans-serif; font-size: 13px; color: #fff; line-height: 22px;
  }
  .contact__row { display: flex; align-items: center; gap: 14px; white-space: nowrap; }
  .contact__item { display: inline-flex; align-items: center; gap: 5px; }
  .contact__icon { width: 11px; height: 11px; fill: #fff; }

  .back-brand { position: absolute; left: 40px; top: 40px; }
  .back-brand .brand__name { font-size: 34px; }
  .back-web {
    margin-top: 8px; font-family: "Open Sans", sans-serif; font-size: 11px;
    letter-spacing: 4px; color: var(--ink-muted);
  }
</style>
</head>
<body>
<main class="canvas">

  <section class="card card--front" aria-label="Business card front">
    <div class="brand">
      <div class="brand__name"><span>Torvane Halbridge</span><span class="brand__dot"></span></div>
      <div class="brand__tagline">"Steady guidance for growing companies"</div>
    </div>

    <div class="band--teal"></div>
    <div class="band--navy"></div>

    <div class="person">
      <div class="person__name">MAREN OAKFIELD</div>
      <div class="person__role">CEO/FOUNDER</div>
    </div>

    <svg class="timeline" width="540" height="24" viewBox="0 0 540 24">
      <line x1="0" y1="12" x2="540" y2="12" stroke="#ffffff" stroke-opacity=".85" stroke-width="1.5"/>
      <g stroke="#ffffff" stroke-width="1.5" fill="#245571">
        <circle cx="70" cy="12" r="6"/>
        <circle cx="165" cy="12" r="6"/>
        <circle cx="260" cy="12" r="6" fill="#ee4a2c"/>
        <circle cx="355" cy="12" r="6"/>
        <circle cx="450" cy="12" r="6"/>
      </g>
    </svg>

    <div class="contact">
      <div class="contact__row">4120 Ledgewood Court, Brackenford, Norland 50218</div>
      <div class="contact__row">
        <span class="contact__item"><svg class="contact__icon" viewBox="0 0 12 12"><path d="M2.5 1l2 .3.8 2.4-1.2 1a6 6 0 0 0 3.2 3.2l1-1.2 2.4.8.3 2c-.3.8-1.2 1.3-2 1.2A9 9 0 0 1 1.3 3c-.1-.8.4-1.7 1.2-2z"/></svg>555 014 2270</span>
        <span class="contact__item"><svg class="contact__icon" viewBox="0 0 12 12"><rect x="3" y="0.5" width="6" height="11" rx="1"/></svg>555 018 3391</span>
        <span class="contact__item"><svg class="contact__icon" viewBox="0 0 12 12"><rect x="0.5" y="2" width="11" height="8" rx="1"/></svg>555 016 7742</span>
        <span class="contact__item"><svg class="contact__icon" viewBox="0 0 12 12"><rect x="0.5" y="2" width="11" height="8" rx="1"/></svg>hello@halbridge.example</span>
      </div>
      <div class="contact__row">
        <span class="contact__item"><svg class="contact__icon" viewBox="0 0 12 12"><circle cx="6" cy="6" r="5.5"/></svg>www.halbridge.example</span>
      </div>
    </div>
  </section>

  <section class="card card--back" aria-label="Business card back">
    <div class="back-brand">
      <div class="brand__name"><span>Torvane Halbridge</span><span class="brand__dot"></span></div>
      <div class="brand__tagline">"Steady guidance for growing companies"</div>
      <div class="back-web">www.halbridge.example</div>
    </div>
  </section>

</main>
</body>
</html>
```